Create banners that convert viewers into buyers!

We provide Online Marketing Solutions for small to medium size businesses from web design, Local SEO, Pay-Per-Click, Social Media and Content Marketing. We've been helping local businesses since 2009 and offer a very high level of service that is rarely matched.

Really like to stay colors of logo like banner ad ideas 2 sample.

Would also like to use a photo of a responsive web design as attached image. (you may use a different layout as image provided may be to big for some dimensions)

Sizes needed:
728x90
300x250
480x60
Updates

Add Slogan: We Drive Traffic & Phone Calls!

Slogan: We Drive Phone Calls & Conversions

Target Market(s)

Small to Medium Size businesses: Main businesses we work with are Home Improvement, Lawyers & Physicians

Industry/Entity Type

Marketing

```html
<!DOCTYPE html>
<html lang="en">
<head>
<meta charset="utf-8">
<title>Brightpath Marketing – Banner Set</title>
<link rel="stylesheet" href="https://fonts.googleapis.com/css2?family=Arimo:wght@400;700&family=Roboto+Condensed:wght@400;700&family=Tinos&display=swap">
<style>
  :root {
    --ink: #0c0c0e;
    --panel: #ffffff;
    --brand-blue: #1d6fc4;
    --glow-blue: #2f86e0;
    --bullet-blue: #3d8fe0;
    --text-light: #ffffff;
    --text-dark: #222222;
    --rule: #6b6b6b;
    --gold-top: #ffe27a;
    --gold-bottom: #e2a21a;
    --orange-top: #ffd23a;
    --orange-bottom: #f29a0c;
    --btn-edge: #8a8a8a;
    --device-a: #2a2e35;
    --device-b: #8c3a26;
    --device-c: #d8dde4;
  }
  * { box-sizing: border-box; margin: 0; padding: 0; }
  html, body { width: 1200px; height: 1094px; overflow: hidden; background: #ffffff; }
  .stage {
    position: relative; width: 756px; height: 690px;
    transform: scale(1.5873); transform-origin: 0 0;
    font-family: "Arimo", Arial, sans-serif;
  }
  .banner {
    position: absolute; overflow: hidden;
    background:
      radial-gradient(ellipse 150px 120px at 0 20%, var(--glow-blue) 0%, rgba(47,134,224,0.35) 45%, transparent 75%),
      var(--ink);
    border: 1px solid #333;
  }
  .showcase {
    position: absolute;
    background: linear-gradient(135deg, var(--device-a) 0%, var(--device-b) 45%, var(--device-c) 70%, var(--device-a) 100%);
    border-radius: 3px;
  }
  .headline {
    position: absolute; color: var(--text-light); font-weight: 700;
    text-shadow: 0 2px 3px rgba(0,0,0,0.9);
    letter-spacing: -0.3px; line-height: 1.08;
  }
  .services { position: absolute; list-style: none; color: var(--text-light); white-space: nowrap; }
  .services li { position: relative; padding-left: 12px; }
  .services li::before {
    content: ""; position: absolute; left: 1px; top: 50%; margin-top: -4px;
    border-left: 6px solid var(--bullet-blue);
    border-top: 4px solid transparent; border-bottom: 4px solid transparent;
  }
  .services.ruled { border-top: 1px solid var(--rule); border-bottom: 1px solid var(--rule); padding: 4px 0; }
  .brand-panel { position: absolute; background: var(--panel); }
  .brand-name {
    color: var(--brand-blue); font-weight: 700; white-space: nowrap;
    display: flex; align-items: center; gap: 4px;
  }
  .brand-dot { width: 7px; height: 7px; border-radius: 50%; background: var(--brand-blue); flex: none; }
  .site-url { color: var(--text-dark); white-space: nowrap; }
  .cta {
    position: absolute; display: flex; align-items: center; justify-content: center; gap: 4px;
    color: #1a1a1a; white-space: nowrap;
  }
  .cta svg { flex: none; }
  .cta-classic {
    font-family: "Tinos", "Times New Roman", serif; text-transform: uppercase;
    background: linear-gradient(var(--gold-top), var(--gold-bottom));
    border: 2px solid var(--btn-edge); box-shadow: 0 1px 2px rgba(0,0,0,0.4);
  }
  .cta-modern {
    font-family: "Arimo", Arial, sans-serif;
    background: linear-gradient(var(--orange-top), var(--orange-bottom));
    border: 1px solid #b86e00; border-radius: 6px;
  }

  /* 300 x 250 */
  .rect { width: 300px; height: 250px; top: 34px; }
  .rect .showcase { left: 22px; top: 10px; width: 156px; height: 124px; }
  .rect .services { left: 190px; top: 32px; width: 106px; font-size: 12px; line-height: 15.5px; }
  .rect .services .tight { font-size: 10.5px; letter-spacing: -0.2px; }
  .rect .headline { left: 0; width: 300px; top: 136px; text-align: center; font-size: 26px; }
  .rect .brand-panel { left: 0; top: 199px; width: 300px; height: 51px; }
  .rect .brand-name { position: absolute; left: 8px; top: 11px; font-size: 13px; gap: 3px; }
  .rect .brand-dot { width: 6px; height: 6px; }
  .rect .site-url { position: absolute; left: 26px; top: 32px; font-size: 12px; }
  .rect .cta { left: 168px; top: 6px; width: 124px; height: 34px; font-size: 15px; }

  /* 728 x 90 */
  .leader { width: 730px; height: 92px; left: 12px; }
  .leader .showcase { left: 12px; top: 4px; width: 168px; height: 84px; }
  .leader .headline { left: 188px; top: 16px; font-size: 28px; }
  .leader .services { left: 450px; top: 8px; font-size: 12.5px; line-height: 15.2px; }
  .leader .brand-panel { left: 574px; top: 0; width: 156px; height: 92px; }
  .leader .brand-name { position: absolute; left: 9px; top: 11px; font-size: 12px; gap: 3px; }
  .leader .brand-dot { width: 6px; height: 6px; }
  .leader .site-url { position: absolute; left: 24px; top: 35px; font-size: 12.5px; }
  .leader .cta { left: 22px; top: 54px; width: 114px; height: 30px; font-size: 14px; }

  /* 480 x 60 */
  .strip { width: 471px; height: 61px; left: 13px; }
  .strip .showcase { left: 6px; top: 3px; width: 98px; height: 55px; }
  .strip .headline {
    left: 113px; top: 4px; font-size: 18px; white-space: nowrap;
    font-family: "Roboto Condensed", "Arial Narrow", sans-serif; letter-spacing: -0.2px;
  }
  .strip .services {
    left: 148px; top: 31px; width: 212px; font-size: 9.5px; line-height: 12px;
    display: flex; flex-wrap: wrap; column-gap: 6px;
  }
  .strip .services li { padding-left: 9px; }
  .strip .services li::before { border-left-width: 5px; border-top-width: 3px; border-bottom-width: 3px; margin-top: -3px; }
  .strip .brand-panel { left: 368px; top: 0; width: 103px; height: 61px; }
  .strip .brand-name { position: absolute; left: 4px; top: 6px; font-size: 8px; gap: 2px; }
  .strip .brand-dot { width: 4px; height: 4px; }
  .strip .site-url { position: absolute; left: 12px; top: 22px; font-size: 8.5px; }
  .strip .cta { left: 12px; top: 36px; width: 78px; height: 20px; font-size: 10px; }
</style>
</head>
<body>
<main class="stage">

  <section class="banner rect" style="left:68px">
    <div class="showcase" role="img" aria-label="Responsive website shown on a desktop monitor, tablet and phone"></div>
    <ul class="services ruled">
      <li>Web Design</li><li>Local SEO</li><li>Pay-Per-Click</li><li>Social Media</li><li class="tight">Content Marketing</li>
    </ul>
    <h2 class="headline">We Drive Traffic &amp;<br>Phone Calls!</h2>
    <div class="brand-panel">
      <div class="brand-name"><span class="brand-dot"></span>Brightpath Marketing</div>
      <div class="site-url">www.yoursite.com</div>
      <a class="cta cta-classic">Learn More
        <svg width="11" height="14" viewBox="0 0 11 14"><path d="M1 1 L1 12 L4 9 L6 13 L8 12 L6 8 L10 8 Z" fill="#111"/></svg>
      </a>
    </div>
  </section>

  <section class="banner rect" style="left:382px">
    <div class="showcase" role="img" aria-label="Responsive website shown on a desktop monitor, tablet and phone"></div>
    <ul class="services ruled">
      <li>Web Design</li><li>Local SEO</li><li>Pay-Per-Click</li><li>Social Media</li><li class="tight">Content Marketing</li>
    </ul>
    <h2 class="headline">We Drive Traffic &amp;<br>Phone Calls!</h2>
    <div class="brand-panel">
      <div class="brand-name"><span class="brand-dot"></span>Brightpath Marketing</div>
      <div class="site-url">www.yoursite.com</div>
      <a class="cta cta-modern" style="font-size:16px">
        <svg width="11" height="14" viewBox="0 0 11 14"><path d="M1 1 L1 12 L4 9 L6 13 L8 12 L6 8 L10 8 Z" fill="#111"/></svg>Learn More
      </a>
    </div>
  </section>

  <section class="banner leader" style="top:300px">
    <div class="showcase" role="img" aria-label="Responsive website shown on a desktop monitor, tablet and phone"></div>
    <h2 class="headline">We Drive Traffic &amp;<br>Phone Calls!</h2>
    <ul class="services">
      <li>Web Design</li><li>Local SEO</li><li>Pay-Per-Click</li><li>Social Media</li><li>Content Marketing</li>
    </ul>
    <div class="brand-panel">
      <div class="brand-name"><span class="brand-dot"></span>Brightpath Marketing</div>
      <div class="site-url">www.yoursite.com</div>
      <a class="cta cta-classic">Learn More
        <svg width="11" height="14" viewBox="0 0 11 14"><path d="M1 1 L1 12 L4 9 L6 13 L8 12 L6 8 L10 8 Z" fill="#111"/></svg>
      </a>
    </div>
  </section>

  <section class="banner leader" style="top:405px">
    <div class="showcase" role="img" aria-label="Responsive website shown on a desktop monitor, tablet and phone"></div>
    <h2 class="headline">We Drive Traffic &amp;<br>Phone Calls!</h2>
    <ul class="services">
      <li>Web Design</li><li>Local SEO</li><li>Pay-Per-Click</li><li>Social Media</li><li>Content Marketing</li>
    </ul>
    <div class="brand-panel">
      <div class="brand-name"><span class="brand-dot"></span>Brightpath Marketing</div>
      <div class="site-url">www.yoursite.com</div>
      <a class="cta cta-modern" style="font-size:16px">
        <svg width="11" height="14" viewBox="0 0 11 14"><path d="M1 1 L1 12 L4 9 L6 13 L8 12 L6 8 L10 8 Z" fill="#111"/></svg>Learn More
      </a>
    </div>
  </section>

  <section class="banner strip" style="top:516px">
    <div class="showcase" role="img" aria-label="Responsive website shown on a desktop monitor, tablet and phone"></div>
    <h2 class="headline">We Drive Traffic &amp; Phone Calls!</h2>
    <ul class="services">
      <li>Web Design</li><li>Local SEO</li><li>Pay-Per-Click</li><li>Social Media</li><li>Content Marketing</li>
    </ul>
    <div class="brand-panel">
      <div class="brand-name"><span class="brand-dot"></span>Brightpath Marketing</div>
      <div class="site-url">www.yoursite.com</div>
      <a class="cta cta-classic">Learn More
        <svg width="8" height="10" viewBox="0 0 11 14"><path d="M1 1 L1 12 L4 9 L6 13 L8 12 L6 8 L10 8 Z" fill="#111"/></svg>
      </a>
    </div>
  </section>

  <section class="banner strip" style="top:587px">
    <div class="showcase" role="img" aria-label="Responsive website shown on a desktop monitor, tablet and phone"></div>
    <h2 class="headline">We Drive Traffic &amp; Phone Calls!</h2>
    <ul class="services">
      <li>Web Design</li><li>Local SEO</li><li>Pay-Per-Click</li><li>Social Media</li><li>Content Marketing</li>
    </ul>
    <div class="brand-panel">
      <div class="brand-name"><span class="brand-dot"></span>Brightpath Marketing</div>
      <div class="site-url">www.yoursite.com</div>
      <a class="cta cta-modern" style="font-size:11px;border-radius:4px">
        <svg width="8" height="10" viewBox="0 0 11 14"><path d="M1 1 L1 12 L4 9 L6 13 L8 12 L6 8 L10 8 Z" fill="#111"/></svg>Learn More
      </a>
    </div>
  </section>

</main>
</body>
</html>
```